Namecard Designs+Logo for a High End Automobile Company

We need a new business card for our company called Nordel Motorwerk.

www.nordelmotorwerk.example.sg
Our new website will be up in 2.5 months time.

We sell used and brand new continental cars like Valcrest, KTR, Almira, Dunvale and etc. Currently we are operating from 2 offices in Singapore and United Kingdom.

We want a design which is serious. We are open to colours but try to keep it at a maximum of 3 colours.

We prefer something simple and minimal. We are open to 2 sides printing or even 2 sided namecards. Both UK and Singapore company offices address must be in; either side by side, front and back, or even 2 sided cards.

The logo can be a text logo, emblem, abstract, pictorial or combination.

We are printing with Printlyx.com so please kindly follow the printing guideline.

http://uk.printlyx.example/help/faq/templates-and-guidelines.html

Rich and Car Enthusiasts

Printing

• Our 2 offices; UK and Singapore.

Our slogan which is " The Automobile Specialist"
• Not more than 3 colours

```html
<!DOCTYPE html>
<html lang="en">
<head>
<meta charset="utf-8">
<title>Nordel Motorwerk – Logo and Business Card</title>
<link rel="stylesheet" href="https://fonts.googleapis.com/css2?family=Michroma&family=Arimo:wght@400;700&display=swap">
<style>
  :root {
    --board: #3a3a3a;
    --board-edge: #262626;
    --card: #000000;
    --ink: #ffffff;
    --silver: #d4d4d4;
    --emblem-red: #e0412f;
    --shadow: rgba(0, 0, 0, 0.6);
  }
  * { margin: 0; padding: 0; box-sizing: border-box; }
  html, body { width: 1200px; height: 900px; overflow: hidden; }
  body {
    position: relative;
    background: radial-gradient(ellipse at 50% 40%, var(--board) 0%, var(--board-edge) 100%);
    font-family: "Arimo", Arial, sans-serif;
    color: var(--ink);
  }
  .board-title {
    position: absolute; left: 18px; top: 54px;
    font-family: "Arimo", Arial, sans-serif;
    font-weight: 700; font-size: 30px; letter-spacing: 0.5px;
  }
  .logo-panel {
    position: absolute; left: 38px; top: 108px; width: 285px; height: 279px;
    background: var(--card);
  }
  .card {
    position: absolute; width: 612px; height: 339px;
    background: var(--card); border-radius: 18px;
    box-shadow: 0 8px 22px var(--shadow);
  }
  .card-back { left: 518px; top: 108px; }
  .card-front { left: 308px; top: 518px; }
  .mark-circle {
    position: absolute; border-radius: 50%; background: var(--emblem-red);
  }
  .brand-rule {
    position: absolute; height: 1px; background: var(--silver);
  }
  .brand-name {
    position: absolute; left: 0; right: 0; text-align: center;
    font-family: "Michroma", sans-serif; color: var(--silver);
    letter-spacing: 1px; white-space: nowrap;
  }
  .logo-panel .mark-circle { width: 110px; height: 110px; left: 88px; top: 62px; }
  .logo-panel .brand-rule { left: 30px; right: 30px; top: 200px; }
  .logo-panel .brand-name { top: 212px; font-size: 15px; }
  .card-back .mark-circle { width: 130px; height: 130px; left: 241px; top: 58px; }
  .card-back .brand-name { top: 215px; font-size: 18px; }
  .website {
    position: absolute; left: 0; right: 0; top: 278px; text-align: center;
    font-family: "Michroma", sans-serif; font-size: 15px; letter-spacing: 1.5px;
  }
  .card-front .mark-circle { width: 86px; height: 86px; left: 77px; top: 30px; }
  .card-front .brand-rule { left: 30px; width: 180px; top: 134px; }
  .card-front .brand-name { left: 20px; right: auto; width: 200px; top: 140px; font-size: 11px; }
  .slogan {
    position: absolute; left: 20px; width: 200px; top: 167px; text-align: center;
    font-weight: 700; font-size: 12px;
  }
  .person { position: absolute; right: 37px; top: 80px; text-align: right; }
  .person-name { font-family: "Michroma", sans-serif; font-size: 17px; letter-spacing: 1px; }
  .person-role { font-family: "Michroma", sans-serif; font-size: 8px; letter-spacing: 1.5px; margin-top: 2px; }
  .contact-list { position: absolute; right: 22px; top: 212px; list-style: none; }
  .contact-list li {
    display: flex; align-items: center; justify-content: flex-end; gap: 10px;
    height: 22px; font-size: 12.5px; white-space: nowrap;
  }
  .contact-icon { width: 18px; height: 16px; fill: none; stroke: var(--ink); stroke-width: 1.6; }
  .contact-icon .solid { fill: var(--ink); stroke: none; }
  .office-tag { font-weight: 700; }
</style>
</head>
<body>
  <h1 class="board-title">LOGO DESIGNED</h1>

  <section class="logo-panel" aria-label="Logo">
    <div class="mark-circle"></div>
    <div class="brand-rule"></div>
    <p class="brand-name">NORDEL MOTORWERK</p>
  </section>

  <section class="card card-back" aria-label="Business card back">
    <div class="mark-circle"></div>
    <p class="brand-name">NORDEL MOTORWERK</p>
    <p class="website">WWW.NORDELMOTORWERK.EXAMPLE.SG</p>
  </section>

  <section class="card card-front" aria-label="Business card front">
    <div class="mark-circle"></div>
    <div class="brand-rule"></div>
    <p class="brand-name">NORDEL MOTORWERK</p>
    <p class="slogan">The Automobile Specialist</p>

    <div class="person">
      <p class="person-name">YOUR NAME</p>
      <p class="person-role">MANAGER</p>
    </div>

    <ul class="contact-list">
      <li><span><span class="office-tag">SG</span> Address Line, District, Postcode</span>
        <svg class="contact-icon" viewBox="0 0 18 16" aria-hidden="true"><path d="M2 8 L9 2 L16 8"/><path d="M4 7 V14 H14 V7"/><rect x="7.5" y="9.5" width="3" height="4.5"/></svg>
      </li>
      <li><span><span class="office-tag">UK</span> Address Line, Town, Postcode</span>
        <svg class="contact-icon" viewBox="0 0 18 16" aria-hidden="true"><path d="M2 8 L9 2 L16 8"/><path d="M4 7 V14 H14 V7"/><rect x="7.5" y="9.5" width="3" height="4.5"/></svg>
      </li>
      <li>0000 000 000
        <svg class="contact-icon" viewBox="0 0 18 16" aria-hidden="true"><path class="solid" d="M2 5 Q9 1 16 5 L15 7 L12 6 L12 5 Q9 4 6 5 L6 6 L3 7 Z"/><rect class="solid" x="4" y="8" width="10" height="6" rx="1"/></svg>
      </li>
      <li>0000 000 000
        <svg class="contact-icon" viewBox="0 0 18 16" aria-hidden="true"><rect x="6" y="1.5" width="6.5" height="13" rx="1"/><rect class="solid" x="7.5" y="3.5" width="3.5" height="5"/></svg>
      </li>
      <li>name@nordelmotorwerk.example.sg
        <svg class="contact-icon" viewBox="0 0 18 16" aria-hidden="true"><rect class="solid" x="2" y="3.5" width="14" height="9" rx="1"/></svg>
      </li>
    </ul>
  </section>
</body>
</html>
```